Business Card Design Project

We need a business card design for our IT Managed Services firm.
Our logo is attached.
More information on our company can be found at:
www.brindlowsys.com
Target Market(s)
CEO, President. Mid Size Businesses
Industry/Entity Type
Business

```html
<!DOCTYPE html>
<html lang="en">
<head>
<meta charset="utf-8">
<title>Brindlow Systems – Business Card Options</title>
<link rel="stylesheet" href="https://fonts.googleapis.com/css2?family=Arimo:wght@400;700&family=Comfortaa:wght@400;700&display=swap">
<style>
  :root {
    --page: #ffffff;
    --ink: #000000;
    --muted: #7a7a7a;
    --rule: #8a8a8a;
    --accent: #e8201c;
    --web: #4a4a4a;
    --grey-base: #efefef;
    --grey-ring: #d6d6d6;
    --grey-band: #cacaca;
    --cyan-base: #e2ffff;
    --cyan-ring: #c2f7f8;
    --cyan-band: #a6fcfc;
    --edge: #b9b9b9;
  }
  * { box-sizing: border-box; margin: 0; padding: 0; }
  html, body {
    width: 1200px; height: 686px; overflow: hidden;
    background: var(--page);
    font-family: "Arimo", Arial, sans-serif;
  }
  .sheet { position: relative; width: 1200px; height: 686px; }

  .card {
    position: absolute; width: 575px; height: 330px;
    border: 1px solid var(--edge); overflow: hidden;
  }
  .card--front.card--grey { left: 2px; top: 2px; }
  .card--front.card--cyan { left: 624px; top: 2px; }
  .card--back.card--grey  { left: 2px; top: 355px; }
  .card--back.card--cyan  { left: 624px; top: 355px; }

  .card__pattern { position: absolute; inset: 0; }
  .card--grey .card__pattern {
    background:
      radial-gradient(circle at 80% 30%, var(--grey-ring) 0%, var(--grey-base) 45%, transparent 70%),
      radial-gradient(circle at 0% 85%, var(--grey-ring) 0%, var(--grey-base) 40%),
      var(--grey-base);
  }
  .card--cyan .card__pattern {
    background:
      radial-gradient(circle at 80% 30%, var(--cyan-ring) 0%, var(--cyan-base) 45%, transparent 70%),
      radial-gradient(circle at 0% 85%, var(--cyan-ring) 0%, var(--cyan-base) 40%),
      var(--cyan-base);
  }

  .brand { position: absolute; display: flex; align-items: center; gap: 6px; }
  .brand__mark { width: 10px; height: 10px; background: var(--accent); flex: none; }
  .brand__name { font-weight: 700; color: var(--ink); white-space: nowrap; }
  .card--front .brand { left: 6px; top: 30px; }
  .card--front .brand__name { font-size: 22px; }

  .contact {
    position: absolute; left: 325px; top: 125px;
    font-size: 14px; font-weight: 700; line-height: 19px; color: var(--ink);
    white-space: nowrap;
  }

  .person { position: absolute; right: 58px; top: 192px; text-align: right; }
  .person__name {
    font-family: "Comfortaa", "Trebuchet MS", sans-serif;
    font-weight: 700; font-size: 24px; color: var(--ink); line-height: 30px;
    white-space: nowrap;
  }
  .person__role {
    font-family: "Comfortaa", "Trebuchet MS", sans-serif;
    font-weight: 400; font-size: 19px; color: var(--muted); line-height: 20px;
  }

  .divider {
    position: absolute; left: 63px; top: 248px; width: 452px; height: 2px;
    background: var(--rule);
  }
  .website {
    position: absolute; left: 66px; top: 261px;
    font-size: 16px; letter-spacing: 0.6em; color: var(--web); white-space: nowrap;
  }

  .card--back .brand {
    left: 0; right: 0; top: 100px; justify-content: center; gap: 12px;
  }
  .card--back .brand__mark { width: 22px; height: 22px; }
  .card--back .brand__name { font-size: 50px; }

  .address-band {
    position: absolute; left: 0; right: 0; bottom: 0; height: 72px;
    display: flex; align-items: center; justify-content: center;
    font-size: 14.5px; font-weight: 700; color: var(--accent); white-space: nowrap;
  }
  .card--grey .address-band { background: var(--grey-band); }
  .card--cyan .address-band { background: var(--cyan-band); }
</style>
</head>
<body>
<main class="sheet">

  <section class="card card--front card--grey">
    <div class="card__pattern" role="img" aria-label="Soft concentric ring background pattern"></div>
    <div class="brand"><span class="brand__mark"></span><span class="brand__name">Brindlow Systems</span></div>
    <p class="contact">Phone No: 456-7102-38815<br>Email: info@brindlowsys.com</p>
    <div class="person"><p class="person__name">Abcdef Ghijaklm</p><p class="person__role">owner</p></div>
    <div class="divider"></div>
    <p class="website">www.brindlowsys.com</p>
  </section>

  <section class="card card--front card--cyan">
    <div class="card__pattern" role="img" aria-label="Soft concentric ring background pattern"></div>
    <div class="brand"><span class="brand__mark"></span><span class="brand__name">Brindlow Systems</span></div>
    <p class="contact">Phone No: 456-7102-38815<br>Email: info@brindlowsys.com</p>
    <div class="person"><p class="person__name">Abcdef Ghijaklm</p><p class="person__role">owner</p></div>
    <div class="divider"></div>
    <p class="website">www.brindlowsys.com</p>
  </section>

  <section class="card card--back card--grey">
    <div class="card__pattern" role="img" aria-label="Soft concentric ring background pattern"></div>
    <div class="brand"><span class="brand__mark"></span><span class="brand__name">Brindlow Systems</span></div>
    <p class="address-band">Address:dfasdklf sdfjsadkfsdaklf sdfhasdflsad flksdfkasdj fsdkflkasdjc</p>
  </section>

  <section class="card card--back card--cyan">
    <div class="card__pattern" role="img" aria-label="Soft concentric ring background pattern"></div>
    <div class="brand"><span class="brand__mark"></span><span class="brand__name">Brindlow Systems</span></div>
    <p class="address-band">Address:dfasdklf sdfjsadkfsdaklf sdfhasdflsad flksdfkasdj fsdkflkasdjc</p>
  </section>

</main>
</body>
</html>
```